Technical Communications firm needs an article turned into a white paper

We want to redesign a 3-part blog series into a white paper that we can print for a conference. I've consolidated the three posts into the attached Word document.

We are looking for a light, easy to read design. Good use of graphics to support the message. I've added the graphics we used in the original post.

You can view them at
http://www.brightquillpages.com/blog/are-you-satisfied-with-your-dita-solution/

Target Market(s)

Product managers from High-tech, Finance, and Medical industries.

Industry/Entity Type

Information Technology

Colors

Designer to choose colors to be used in the design.

Requirements
Must have
• Must be modern, light, easy to read and slick design. Try to incorporate the graphics provided, but feel free to add more. Must retain the lists and tables.
• Must align with our website/brand.
• Must be easy to read. So not too busy.
• Please move all footnotes to endnotes. You'll need to rework the numbering.
Nice to have
• Awesome coverpage.
Should not have
• Hokey clipart. Not too heavy or hard to read.

```html
<!DOCTYPE html>
<html lang="en">
<head>
<meta charset="utf-8">
<title>Bright Quill Pages – White Paper Cover</title>
<link rel="stylesheet" href="https://fonts.googleapis.com/css2?family=Exo+2:wght@400;600;700&family=Open+Sans:wght@400&display=swap">
<style>
  :root {
    --backdrop: #e8e5e0;
    --paper: #ffffff;
    --brand-blue: #0a8fd6;
    --brand-blue-deep: #1565c0;
    --brand-navy: #1c3a8a;
    --swoosh-grey: #b9bec6;
    --sky-top: #aeb8c2;
    --sky-low: #e6ebef;
    --field: #5d9a3c;
    --ink-light: #ffffff;
    --ink-muted: #5d6670;
  }
  * { margin: 0; padding: 0; box-sizing: border-box; }
  html, body { width: 1200px; height: 804px; overflow: hidden; }
  body {
    background: var(--backdrop);
    display: flex;
    align-items: center;
    justify-content: center;
    font-family: "Open Sans", sans-serif;
  }
  .cover {
    position: relative;
    width: 520px;
    height: 728px;
    background: var(--paper);
    box-shadow: 0 6px 22px rgba(0,0,0,.18);
    overflow: hidden;
  }
  .cover-art { position: absolute; inset: 0; width: 100%; height: 100%; }
  .brand {
    position: absolute;
    top: 42px;
    right: 40px;
    display: flex;
    align-items: center;
    gap: 8px;
    font-family: "Exo 2", sans-serif;
    font-weight: 700;
    font-size: 17px;
    line-height: 1;
    color: var(--brand-navy);
    letter-spacing: .2px;
  }
  .brand-dot {
    width: 26px; height: 26px;
    border-radius: 50%;
    background: var(--brand-navy);
  }
  .headline {
    position: absolute;
    left: 0; right: 0;
    top: 462px;
    text-align: center;
    font-family: "Exo 2", sans-serif;
    color: var(--ink-light);
  }
  .headline-kicker {
    font-size: 16px;
    font-weight: 400;
    letter-spacing: .5px;
    text-transform: uppercase;
  }
  .headline-main {
    margin-top: 4px;
    font-size: 30px;
    font-weight: 700;
    text-transform: uppercase;
  }
  .headline-main .accent { color: var(--brand-navy); }
  .headline-rule {
    width: 330px;
    height: 1px;
    margin: 8px auto 8px;
    background: rgba(255,255,255,.7);
  }
  .headline-lede {
    font-family: "Open Sans", sans-serif;
    font-size: 11px;
    line-height: 1.45;
    width: 340px;
    margin: 0 auto;
  }
  .site-url {
    position: absolute;
    left: 0; right: 0;
    top: 663px;
    text-align: center;
    font-size: 11px;
    letter-spacing: 2.4px;
    color: var(--ink-muted);
  }
</style>
</head>
<body>
  <main class="cover">
    <svg class="cover-art" viewBox="0 0 520 728" preserveAspectRatio="none" aria-hidden="false">
      <defs>
        <linearGradient id="field-photo" x1="0" y1="0" x2="0" y2="1">
          <stop offset="0" stop-color="var(--sky-top)"/>
          <stop offset=".55" stop-color="var(--sky-low)"/>
          <stop offset=".72" stop-color="#9fc07f"/>
          <stop offset="1" stop-color="var(--field)"/>
        </linearGradient>
        <linearGradient id="panel-blue" x1="0" y1="0" x2="0" y2="1">
          <stop offset="0" stop-color="var(--brand-blue)"/>
          <stop offset="1" stop-color="#0a85cc"/>
        </linearGradient>
      </defs>

      <!-- top swoosh -->
      <path class="swoosh-grey" d="M0 105 C150 170 330 175 520 110 L520 140 C330 200 150 195 0 140 Z" fill="var(--swoosh-grey)"/>
      <path class="swoosh-blue" d="M0 88 C150 150 330 160 520 92 L520 110 C330 180 150 172 0 115 Z" fill="var(--brand-blue)"/>

      <!-- photograph area -->
      <path role="img" aria-label="Photo: businessman relaxing in an office chair in an open green field under a pale sky"
            d="M0 140 C150 195 330 200 520 140 L520 380 C380 350 240 360 0 440 Z"
            fill="url(#field-photo)"/>

      <!-- lower swoosh and blue panel -->
      <path class="swoosh-grey" d="M0 430 C200 350 360 340 520 368 L520 385 C360 360 200 375 0 455 Z" fill="var(--swoosh-grey)"/>
      <path class="panel" d="M0 450 C200 372 360 362 520 380 L520 618 L0 618 Z" fill="url(#panel-blue)"/>
      <path d="M0 450 C200 372 360 362 520 380" fill="none" stroke="#ffffff" stroke-width="2" opacity=".8"/>
      <path d="M20 470 C200 400 360 392 520 404" fill="none" stroke="#ffffff" stroke-width=".8" opacity=".35"/>
      <path d="M40 482 C210 414 360 408 520 418" fill="none" stroke="#ffffff" stroke-width=".8" opacity=".25"/>

      <!-- bottom rules -->
      <rect x="0" y="618" width="520" height="4" fill="var(--swoosh-grey)"/>
      <rect x="0" y="628" width="520" height="3" fill="var(--brand-blue)"/>
      <rect x="0" y="690" width="520" height="6" fill="var(--brand-blue)"/>
      <rect x="0" y="698" width="520" height="2" fill="var(--swoosh-grey)"/>
    </svg>

    <div class="brand">
      <span class="brand-dot"></span>
      <span class="brand-name">BRIGHTQUILLPAGES.com</span>
    </div>

    <section class="headline">
      <p class="headline-kicker">Are you satisfied with</p>
      <h1 class="headline-main">Your DITA <span class="accent">Solution?</span></h1>
      <div class="headline-rule"></div>
      <p class="headline-lede">We design innovative, scalable, and sustainable intelligent content solutions for authoring, managing, and publishing high-value content.</p>
    </section>

    <p class="site-url">www.brightquillpages.com</p>
  </main>
</body>
</html>
```